Website Design for R W Builders: Showcasing Excellence in General Contracting

R W Builders, a leading general contractor based in California, is seeking a professional and engaging website design to effectively showcase our expertise, services, and commitment to excellence. The website will serve as a digital platform to represent our brand identity, highlight our portfolio, and attract potential clients in various sectors.

Key Objectives:

Reflect Company Identity: The website should accurately reflect the identity and values of R W Builders, including our dedication to quality, professionalism, and client satisfaction.
Showcase Services: Highlight our wide range of general contracting services, including but not limited to construction management, design-build, renovation, and commercial construction.
Portfolio Display: Display an extensive portfolio of past projects completed by R W Builders, showcasing our capabilities, craftsmanship, and successful outcomes.
Client Testimonials: Incorporate client testimonials and case studies to demonstrate our track record of delivering projects on time, within budget, and to the highest standards.
Contact Information: Ensure easy access to contact information, including phone number, email, and physical address, to facilitate communication with potential clients.
Responsive Design: Develop a responsive website design optimized for various devices and screen sizes, ensuring a seamless user experience across desktops, laptops, tablets, and smartphones.
Search Engine Optimization (SEO): Implement SEO best practices to enhance the visibility of the website on search engines, increasing organic traffic and generating leads.
User-Friendly Navigation: Create an intuitive and user-friendly navigation structure that enables visitors to easily find the information they need, such as services, portfolio, testimonials, and contact details.
Visual Appeal: Utilize visually appealing graphics, images, and layout designs to capture the attention of visitors and leave a lasting impression of professionalism and quality.
Compliance and Security: Ensure compliance with industry standards and regulations, as well as implementing necessary security measures to protect user data and privacy.

```html
<!DOCTYPE html>
<html lang="en">
<head>
<meta charset="UTF-8">
<title>R W Builders — General Contracting</title>
<link href="https://fonts.googleapis.com/css2?family=Oswald:wght@300;400;500;600;700&family=Tinos&display=swap" rel="stylesheet">
<style>
:root{
  --black:#0b0b0b;
  --white:#ffffff;
  --ink:#1a1a1a;
  --grey-bg:#f1f1f1;
  --muted:#444;
  --star:#e3b23c;
  --line:#d8d8d8;
}
*{margin:0;padding:0;box-sizing:border-box}
html,body{width:1200px;height:4491px;overflow:hidden}
body{position:relative;background:var(--white);font-family:'Oswald',sans-serif;color:var(--ink)}
.abs{position:absolute}
.btn{position:absolute;display:flex;align-items:center;justify-content:center;font-size:15px;font-weight:400}
.btn-dark{background:var(--black);color:var(--white)}
.btn-light{background:var(--white);color:var(--black)}
.section-title{position:absolute;left:0;width:1200px;text-align:center;font-weight:700;font-size:46px;letter-spacing:.5px;text-transform:uppercase;color:var(--black)}
.section-title::after{content:"";display:block;width:30px;height:4px;background:var(--black);border-radius:2px;margin:4px auto 0;transform:translateX(14px) skewX(-20deg)}
.arrow{position:absolute;width:32px;height:32px;border-radius:50%;background:var(--white);border:1px solid #ddd;box-shadow:0 1px 4px rgba(0,0,0,.2);display:flex;align-items:center;justify-content:center}
.photo{position:absolute}

/* hero */
.hero{left:0;top:0;width:1200px;height:611px;background:linear-gradient(180deg,#3d4a55 0%,#8a6b45 40%,#c98a3e 60%,#4a3320 100%)}
.brand{position:absolute;left:104px;top:60px;width:150px;text-align:center;color:var(--white)}
.brand-name{font-weight:700;font-size:30px;line-height:1;letter-spacing:.5px}
.brand-city{font-weight:600;font-size:13px;margin-top:6px;letter-spacing:1px}
.nav{position:absolute;top:30px;left:463px;display:flex;gap:40px;color:var(--white);font-size:14px}
.nav a{color:inherit;text-decoration:none;padding-bottom:8px}
.nav a.active{border-bottom:2px solid var(--white)}
.hero-welcome{left:112px;top:212px;color:var(--white);font-size:32px;font-weight:400}
.hero-bar{left:0;top:269px;width:497px;height:76px;background:var(--black)}
.hero-title{left:112px;top:268px;color:var(--white);font-size:58px;font-weight:600;line-height:76px}
.hero-sub{left:112px;top:360px;color:var(--white);font-size:21px;font-weight:500}

/* services */
.service-card{position:absolute;top:792px;width:316px;height:380px;background:var(--white);box-shadow:0 2px 8px rgba(0,0,0,.2)}
.service-card .photo{left:12px;top:14px;width:292px;height:298px}
.service-card .label{position:absolute;left:20px;top:330px;font-size:22px;font-weight:600}
.service-card .btn{left:211px;top:326px;width:92px;height:36px}

/* about */
.about-bg{left:0;top:1261px;width:1200px;height:551px;background:var(--grey-bg)}
.about-title{left:642px;top:1300px;font-size:46px;font-weight:700}
.about-title::after{content:"";display:block;width:26px;height:4px;background:var(--black);margin:-2px 0 0 86px;transform:skewX(-20deg)}
.about-text{left:642px;top:1394px;width:440px;font-size:12.5px;font-weight:300;line-height:28px;color:var(--ink)}
.about-text p{margin-bottom:11px}

/* values band */
.values{left:0;top:1812px;width:1200px;height:211px;background:var(--black);display:flex}
.value{flex:1;display:flex;flex-direction:column;align-items:center;padding-top:52px;color:var(--white);text-align:center;font-size:14px;line-height:22px;border-right:2px dashed #cfcfcf}
.value:last-child{border-right:none}
.value .icon{width:64px;height:64px;background:var(--white);margin-bottom:14px;display:flex;align-items:center;justify-content:center}

/* general contracting */
.gc-tile{position:absolute;top:2205px;height:399px}
.gc-tile .cap{position:absolute;left:20px;bottom:16px;color:var(--white);font-size:26px;font-weight:600}

/* testimonials */
.testi-bg{left:0;top:2695px;width:1200px;height:493px;background:linear-gradient(180deg,#f4f4f4,#e9e9e9)}
.testi{position:absolute;top:2900px;width:440px}
.avatar{position:absolute;left:8px;top:0;width:80px;height:80px;border-radius:50%;background:#6b6b6b}
.testi .who{position:absolute;left:108px;top:20px;font-size:13px;font-weight:500;line-height:20px}
.testi .stars{color:var(--star);font-size:10px;letter-spacing:1px}
.testi .quote{position:absolute;left:0;top:102px;width:440px;font-size:12.5px;font-weight:300;line-height:28px;text-align:justify}
.testi-divider{left:594px;top:2972px;width:2px;height:120px;background:var(--black)}

/* portfolio */
.overlay-text{position:absolute;left:112px;top:3394px;width:216px;height:270px;background:rgba(20,20,20,.85);color:var(--white);padding:60px 0 0 20px;font-size:16px;font-weight:500;line-height:30px}
.overlay-text .val{font-size:20px}

/* footer */
.footer{left:0;top:4091px;width:1200px;height:400px;background:#151515;color:var(--white)}
.footer-brand{left:110px;top:4245px;width:170px;text-align:center;color:var(--white)}
.footer-brand .brand-name{font-size:32px}
.footer-col{position:absolute;top:4186px;color:var(--white)}
.footer-col h4{font-size:19px;font-weight:500;margin-bottom:18px}
.footer-col li{list-style:none;font-size:12.5px;font-weight:300;line-height:28px}
.footer-div{top:4196px;width:2px;height:185px;background:#ccc}
.contact-row{display:flex;align-items:flex-start;gap:16px;font-size:12.5px;font-weight:300;line-height:20px;margin-bottom:22px}
.copyright{left:0;top:4456px;width:1200px;text-align:center;font-family:'Tinos',serif;font-size:12.5px;letter-spacing:.5px;color:#eee}
</style>
</head>
<body>

<!-- HERO -->
<section class="abs hero" role="img" aria-label="Excavator digging at a construction site under a sunset sky"></section>
<div class="brand">
  <div class="brand-name">R W Builders</div>
  <div class="brand-city">LINDEN VALE, CA</div>
</div>
<nav class="nav">
  <a class="active">Home</a><a>About Us</a><a>Services</a><a>Portfolio</a><a>Testimonials</a>
</nav>
<div class="btn btn-light" style="left:956px;top:23px;width:122px;height:43px">Contact Us</div>
<div class="abs hero-welcome">Welcome To</div>
<div class="abs hero-bar"></div>
<h1 class="abs hero-title">R W Builders</h1>
<div class="abs hero-sub">An 8(a) Small Business Prime Contractor</div>
<div class="btn btn-light" style="left:112px;top:424px;width:123px;height:43px">Get Started</div>

<!-- SPECIALIZED SERVICES -->
<h2 class="section-title" style="top:686px">Specialized Services</h2>
<div class="arrow" style="left:22px;top:959px"><svg width="14" height="14" viewBox="0 0 14 14"><path d="M12 7H2M6 3L2 7l4 4" stroke="#111" fill="none" stroke-width="1.5"/></svg></div>
<div class="arrow" style="left:1127px;top:952px"><svg width="14" height="14" viewBox="0 0 14 14"><path d="M2 7h10M8 3l4 4-4 4" stroke="#111" fill="none" stroke-width="1.5"/></svg></div>
<div class="service-card" style="left:112px">
  <div class="photo" role="img" aria-label="Site worker in hard hat and safety vest overseeing rebar work" style="background:linear-gradient(160deg,#6b5a4a,#c46a2a 55%,#3a3a3a)"></div>
  <div class="label">Site Work</div><div class="btn btn-dark">View</div>
</div>
<div class="service-card" style="left:441px">
  <div class="photo" role="img" aria-label="Excavators and haul trucks working in a mountain quarry" style="background:linear-gradient(180deg,#9bb0b8,#6d7a72 50%,#8a6b3c)"></div>
  <div class="label">Excavation</div><div class="btn btn-dark">View</div>
</div>
<div class="service-card" style="left:771px">
  <div class="photo" role="img" aria-label="Technician servicing an elevator control panel" style="background:linear-gradient(90deg,#3f5a8a,#8c8f96 50%,#d6d6d8)"></div>
  <div class="label">Elevator</div><div class="btn btn-dark">View</div>
</div>

<!-- ABOUT -->
<div class="abs about-bg"></div>
<div class="photo" role="img" aria-label="Engineer with blueprints overlooking a high-rise construction site" style="left:0;top:1261px;width:555px;height:551px;background:linear-gradient(170deg,#b9c6cf,#8f9aa0 45%,#5c5a55)"></div>
<h2 class="abs about-title">ABOUT US</h2>
<div class="abs about-text">
  <p>Since 2013, R W Builders has been a thriving 8(a) certified General Contractor, consistently delivering successful projects to a diverse array of clients.</p>
  <p>Dale Morrow, the sole owner and CEO/President of R W Builders (RWB) originally started the company in 2013. Since, RWB has been a thriving 8(a) certified General Contractor, consistently deliv The company has developed experience with civil, concrete, paving, grading and other small purchase order type projects.</p>
  <p>In addition to work performed in its primary NAICS, R W Builders has also built playgrounds, erected fencing, and paved parking areas; and has performed demolition in buildings/structures, site grading, foundation work, and septic repairs.</p>
</div>
<div class="btn btn-dark" style="left:642px;top:1692px;width:92px;height:35px;font-size:13px">Read More</div>

<!-- VALUES -->
<div class="abs values">
  <div class="value"><div class="icon"><svg width="40" height="40" viewBox="0 0 40 40" fill="none" stroke="#111" stroke-width="2"><circle cx="20" cy="20" r="6"/><circle cx="8" cy="8" r="4"/><circle cx="32" cy="8" r="4"/><circle cx="8" cy="32" r="4"/><circle cx="32" cy="32" r="4"/><path d="M11 11l5 5M29 11l-5 5M11 29l5-5M29 29l-5-5"/></svg></div>Quickly mobilize<br>assets + personnel</div>
  <div class="value"><div class="icon"><svg width="40" height="40" viewBox="0 0 40 40" fill="none" stroke="#111" stroke-width="2"><circle cx="20" cy="20" r="15"/><circle cx="20" cy="20" r="10"/><path d="M15 20l4 4 7-8"/></svg></div>Commitment to<br>quality + safety</div>
  <div class="value"><div class="icon"><svg width="40" height="40" viewBox="0 0 40 40" fill="none" stroke="#111" stroke-width="2"><circle cx="22" cy="22" r="12"/><path d="M6 20a14 14 0 0 1 14-14"/><path d="M25 17h-4a2 2 0 0 0 0 5h2a2 2 0 0 1 0 5h-4M22 14v16"/></svg></div>Complete projects<br>on time + on budget</div>
  <div class="value"><div class="icon"><svg width="40" height="40" viewBox="0 0 40 40" fill="none" stroke="#111" stroke-width="2"><circle cx="20" cy="12" r="5"/><circle cx="9" cy="16" r="4"/><circle cx="31" cy="16" r="4"/><path d="M11 34v-6a9 9 0 0 1 18 0v6M3 32v-4a6 6 0 0 1 6-6M37 32v-4a6 6 0 0 0-6-6"/></svg></div>Qualified field +<br>office staff</div>
  <div class="value"><div class="icon"><svg width="40" height="40" viewBox="0 0 40 40" fill="none" stroke="#111" stroke-width="2"><path d="M11 14a9 9 0 0 1 18 0z"/><path d="M9 14h22"/><rect x="14" y="16" width="12" height="9" rx="3"/><path d="M8 36v-4a7 7 0 0 1 7-7h10a7 7 0 0 1 7 7v4"/></svg></div>Value engineering<br>Commitment to</div>
</div>

<!-- GENERAL CONTRACTING -->
<h2 class="section-title" style="top:2104px">General Contracting</h2>
<div class="arrow" style="left:32px;top:2406px"><svg width="14" height="14" viewBox="0 0 14 14"><path d="M12 7H2M6 3L2 7l4 4" stroke="#111" fill="none" stroke-width="1.5"/></svg></div>
<div class="arrow" style="left:1136px;top:2399px"><svg width="14" height="14" viewBox="0 0 14 14"><path d="M2 7h10M8 3l4 4-4 4" stroke="#111" fill="none" stroke-width="1.5"/></svg></div>
<div class="gc-tile" role="img" aria-label="Tower crane beside high-rise buildings under construction" style="left:112px;width:314px;background:linear-gradient(180deg,#b7c1c9,#6e7378 60%,#2a2d33)"><span class="cap">Preconstructions</span></div>
<div class="gc-tile" role="img" aria-label="Hands reviewing architectural plans with pencil and tape measure" style="left:441px;width:316px;background:linear-gradient(180deg,#e4e6ec,#b9bcc8 55%,#3a3d55)"><span class="cap">Design-Build</span></div>
<div class="gc-tile" role="img" aria-label="Two supervisors in hard hats and vests on a jobsite" style="left:773px;width:314px;background:linear-gradient(180deg,#7c8a96,#c2713a 55%,#2e2f3a)"><span class="cap">Jobsite Supervision</span></div>

<!-- TESTIMONIALS -->
<div class="abs testi-bg" role="img" aria-label="Faint background of construction workers"></div>
<h2 class="section-title" style="top:2744px">Client Testimonials</h2>
<div class="arrow" style="left:32px;top:2972px"><svg width="14" height="14" viewBox="0 0 14 14"><path d="M12 7H2M6 3L2 7l4 4" stroke="#111" fill="none" stroke-width="1.5"/></svg></div>
<div class="arrow" style="left:1136px;top:2965px"><svg width="14" height="14" viewBox="0 0 14 14"><path d="M2 7h10M8 3l4 4-4 4" stroke="#111" fill="none" stroke-width="1.5"/></svg></div>
<div class="testi" style="left:112px">
  <div class="avatar" role="img" aria-label="Client portrait"></div>
  <div class="who">HARLOW FIELD, CA<br>AIR WING<br><span class="stars">★★★★★</span></div>
  <p class="quote">Lorem ipsum dolor sit amet, consectetur adipiscing elit, sed do eiusmod tempor incididunt ut labore et dolore magna aliqua. Ut enim ad minim veniam, quis nostrud exercitation ullamco laboris nisi ut aliquip ex ea commodo consequat.</p>
</div>
<div class="abs testi-divider"></div>
<div class="testi" style="left:644px">
  <div class="avatar" role="img" aria-label="Client portrait"></div>
  <div class="who">CAMP RIDGEWAY, CA<br>FIELD COMMAND<br><span class="stars">★★★★★</span></div>
  <p class="quote">Lorem ipsum dolor sit amet, consectetur adipiscing elit, sed do eiusmod tempor incididunt ut labore et dolore magna aliqua. Ut enim ad minim veniam, quis nostrud exercitation ullamco laboris nisi ut aliquip ex ea commodo consequat.</p>
</div>

<!-- PORTFOLIO -->
<h2 class="section-title" style="top:3272px">Our Portfolio</h2>
<div class="photo" role="img" aria-label="Renovated building corridor with patterned tile floor" style="left:112px;top:3394px;width:488px;height:270px;background:linear-gradient(90deg,#8a8a8a,#e8e8e6 60%,#cfcfcf)"></div>
<div class="overlay-text">Building Renovation<br>B. 6408<br>State Facilities Dept<br>Camp Halden, CA Value:<br><span class="val">$1,001,747</span></div>
<div class="photo" role="img" aria-label="Modern glass office building" style="left:609px;top:3394px;width:298px;height:270px;background:linear-gradient(180deg,#6fa6d8,#8fb6d4 50%,#9a9a92)"></div>
<div class="photo" role="img" aria-label="Dark glass tower against a blue sky" style="left:916px;top:3394px;width:172px;height:270px;background:linear-gradient(180deg,#4d8fd0,#1e3450)"></div>
<div class="photo" role="img" aria-label="Airport control tower with a plane overhead" style="left:112px;top:3682px;width:298px;height:253px;background:linear-gradient(180deg,#3f8ed6,#9ac6ea 60%,#c88a86)"></div>
<div class="photo" role="img" aria-label="Engineers inspecting red industrial piping" style="left:417px;top:3682px;width:298px;height:253px;background:linear-gradient(90deg,#8c1d1d,#c9c9c2 50%,#9a1e1e)"></div>
<div class="photo" role="img" aria-label="Worker in hard hat by warm industrial lights" style="left:724px;top:3682px;width:363px;height:253px;background:linear-gradient(135deg,#1f2a33,#9b5a2a 55%,#2b2a28)"></div>
<div class="btn btn-dark" style="left:555px;top:3966px;width:90px;height:38px;font-size:14px">View All</div>

<!-- FOOTER -->
<footer class="abs footer" role="img" aria-label="Dark faint background of construction machinery"></footer>
<div class="abs footer-brand">
  <div class="brand-name">R W Builders</div>
  <div class="brand-city" style="font-size:15px">LINDEN VALE, CA</div>
</div>
<div class="footer-col" style="left:440px">
  <h4>Quick Links</h4>
  <ul><li>Home</li><li>About Us</li><li>Services</li><li>Portfolio</li><li>Testimonials</li><li>Contact Us</li></ul>
</div>
<div class="abs footer-div" style="left:603px"></div>
<div class="footer-col" style="left:670px">
  <h4>Help Links</h4>
  <ul><li>Privacy Policy</li><li>Terms &amp; Conditions</li></ul>
  <h4 style="margin-top:30px">Follow Us</h4>
  <div style="display:flex;gap:14px">
    <span style="width:16px;height:16px;border-radius:50%;background:#fff;display:block"></span>
    <span style="width:16px;height:16px;border-radius:50%;background:#fff;display:block"></span>
    <span style="width:16px;height:16px;border-radius:50%;background:#fff;display:block"></span>
    <span style="width:16px;height:16px;border-radius:50%;background:#fff;display:block"></span>
  </div>
</div>
<div class="abs footer-div" style="left:844px"></div>
<div class="footer-col" style="left:928px">
  <h4>Contact Info</h4>
  <div class="contact-row"><svg width="14" height="18" viewBox="0 0 14 18"><path d="M7 0a7 7 0 0 0-7 7c0 5 7 11 7 11s7-6 7-11a7 7 0 0 0-7-7zm0 10a3 3 0 1 1 0-6 3 3 0 0 1 0 6z" fill="#fff"/></svg><span>P.O. Box 2210<br>Linden Vale, CA 93100</span></div>
  <div class="contact-row"><svg width="16" height="16" viewBox="0 0 16 16"><path d="M3 1l3 3-2 2c1 3 3 5 6 6l2-2 3 3-2 2C7 15 1 9 1 3z" fill="#fff"/></svg><span>(555) 410-2286</span></div>
  <div class="contact-row"><svg width="16" height="12" viewBox="0 0 16 12"><rect width="16" height="12" fill="#fff"/><path d="M0 0l8 7 8-7" stroke="#151515" fill="none" stroke-width="1.5"/></svg><span>info@rwbuilders.example</span></div>
</div>
<div class="abs" style="left:112px;top:4440px;width:976px;height:1px;background:#888"></div>
<div class="abs copyright">Copyright © 2024 R W Builders - All Rights Reserved.</div>

</body>
</html>
```